Realty Group Needs Classy, Contemporary Letterhead Design

We need a letterhead design for a new realty company located in NY, USA. We buy investment properties to rehabilitate and or keep in our rental portfolio.

```html
<!DOCTYPE html>
<html lang="en">
<head>
<meta charset="utf-8">
<title>Northwick Realty Group – Letterhead</title>
<link href="https://fonts.googleapis.com/css2?family=Carlito:wght@400&family=Poppins:wght@400;500;700&display=swap" rel="stylesheet">
<style>
  :root {
    --brand-purple: #4e2a84;
    --band-grey: #8a8a8a;
    --ink: #3a3a3a;
    --ink-dark: #222222;
    --paper: #ffffff;
    --backdrop: #e2e2e2;
    --signature-tone: #eeeeee;
  }
  * { margin: 0; padding: 0; box-sizing: border-box; }
  html, body {
    width: 1200px; height: 1200px; overflow: hidden;
    background: var(--backdrop);
  }
  .letterhead {
    position: absolute; left: 235px; top: 84px;
    width: 730px; height: 1033px;
    background: var(--paper);
    box-shadow: 0 4px 14px rgba(0,0,0,0.12);
    overflow: hidden;
  }
  .brand {
    position: absolute; left: 52px; top: 82px;
    display: flex; align-items: center; gap: 9px;
    font-family: "Poppins", sans-serif; font-weight: 700;
    color: var(--brand-purple);
  }
  .brand-mark {
    width: 14px; height: 14px; border-radius: 50%;
    background: var(--brand-purple); flex: none;
  }
  .brand-name { font-size: 21px; line-height: 24px; letter-spacing: 0.3px; }
  .sender {
    position: absolute; left: 511px; top: 76px;
    font-family: "Poppins", sans-serif; color: var(--ink-dark);
  }
  .sender-name {
    font-size: 17px; font-weight: 500; color: var(--brand-purple);
    line-height: 22px; margin-bottom: 1px;
  }
  .sender-line {
    display: flex; align-items: center; gap: 5px;
    font-size: 11.5px; line-height: 15.5px;
  }
  .sender-line svg { width: 9px; height: 9px; fill: var(--brand-purple); }
  .letter {
    position: absolute; left: 55px; width: 619px;
    font-family: "Carlito", "Calibri", sans-serif; color: var(--ink);
    font-size: 13.5px;
  }
  .recipient { top: 222px; line-height: 17.7px; font-style: normal; }
  .salutation { top: 350px; line-height: 18px; }
  .body-copy { top: 393px; line-height: 22.1px; text-align: justify; }
  .closing { top: 695px; line-height: 18px; }
  .signature {
    position: absolute; left: 55px; top: 724px;
    width: 248px; height: 77px;
    background: linear-gradient(90deg, var(--signature-tone), #f7f7f7);
    border-radius: 4px;
  }
  .footer-address {
    position: absolute; left: 53px; top: 987px;
    font-family: "Poppins", sans-serif; font-size: 12px; line-height: 16px;
    color: var(--ink-dark);
  }
  .footer-bands { position: absolute; left: 0; top: 995px; width: 730px; height: 38px; }
  .footer-web {
    position: absolute; left: 563px; top: 1004px;
    font-family: "Poppins", sans-serif; font-size: 11.5px; line-height: 16px;
    color: #ffffff; letter-spacing: 0.3px;
  }
</style>
</head>
<body>
  <main class="letterhead">
    <header>
      <div class="brand">
        <span class="brand-mark"></span>
        <span class="brand-name">NORTHWICK<br>REALTY GROUP, LLC</span>
      </div>
      <div class="sender">
        <div class="sender-name">DANIEL MARSH</div>
        <div class="sender-line">
          <svg viewBox="0 0 24 24"><path d="M6.6 10.8a15.2 15.2 0 0 0 6.6 6.6l2.2-2.2c.3-.3.7-.4 1-.2 1.1.4 2.3.6 3.6.6.6 0 1 .4 1 1V20c0 .6-.4 1-1 1C10.6 21 3 13.4 3 4c0-.6.4-1 1-1h3.5c.6 0 1 .4 1 1 0 1.3.2 2.5.6 3.6.1.3 0 .7-.2 1z"/></svg>
          <span>555.214.7730</span>
        </div>
        <div class="sender-line">
          <svg viewBox="0 0 24 24"><path d="M6.6 10.8a15.2 15.2 0 0 0 6.6 6.6l2.2-2.2c.3-.3.7-.4 1-.2 1.1.4 2.3.6 3.6.6.6 0 1 .4 1 1V20c0 .6-.4 1-1 1C10.6 21 3 13.4 3 4c0-.6.4-1 1-1h3.5c.6 0 1 .4 1 1 0 1.3.2 2.5.6 3.6.1.3 0 .7-.2 1z"/></svg>
          <span>555.214.7731</span>
        </div>
        <div class="sender-line">
          <svg viewBox="0 0 24 24"><path d="M3 5h18v14H3zM4.5 6.5 12 12l7.5-5.5v-.2h-15z"/></svg>
          <span>daniel@northwickrealty.com</span>
        </div>
      </div>
    </header>

    <address class="letter recipient">
      Mr. John Doe<br>President<br>Strategy Accountants<br>111 Street Name,<br>City State, 12345
    </address>

    <p class="letter salutation">Dear :</p>

    <div class="letter body-copy">
      <p>Lorem ipsum dolor sit amet, consectetur adipiscing elit. Aenean ut ipsum eget massa hendrerit vestibulum vel in velit. Donec pretium neque velit.</p>
      <p>Aliquam porta lectus nec mauris ornare venenatis. Vivamus non est turpis, et cursus sem. Mauris vehicula erat in diam auctor at bibendum nisl lacinia.</p>
      <p>Morbi imperdiet neque vehicula nunc convallis gravida. Vestibulum iaculis pretium placerat. Integer consequat, est sit amet facilisis eleifend, nibh nibh varius orci, eget dapibus arcu dui non purus. Pellentesque in magna mauris. Duis enim sapien, dictum vitae condimentum a, pulvinar vel lacus. Mauris et molestie nibh. Vestibulum vitae nulla at metus elementum porta sit amet interdum elit. Nulla sollicitudin neque eu nulla volutpat congue.</p>
      <p>Etiam pellentesque, velit id dapibus fermentum, turpis sapien ornare dui, ac tincidunt ligula odio congue purus. Nunc sed ante dui, in porta lectus. Cras nec sem lorem. In hac habitasse platea dictumst. Maecenas id diam quis dui porta tristique. Sed id egestas felis. Donec ullamcorper mattis posuere. Phasellus fermentum eleifend tortor vel dapibus. Vestibulum ante ipsum.</p>
    </div>

    <p class="letter closing">Sincerely,</p>
    <div class="signature" role="img" aria-label="Handwritten signature of Daniel Marsh"></div>

    <footer>
      <div class="footer-address">123 Main Street, Anytown CA 12345</div>
      <svg class="footer-bands" viewBox="0 0 730 38" preserveAspectRatio="none">
        <path d="M0 18.5 H517 Q521 18.5 523 16 L524 15 V26 H0 Z" fill="var(--band-grey)"/>
        <rect x="0" y="18.5" width="521" height="7.5" fill="var(--band-grey)"/>
        <path d="M0 28 H527 Q532 28 536 23 L547 6 Q549 3 553 3 H730 V33 H0 Z" fill="var(--brand-purple)"/>
      </svg>
      <div class="footer-web">www.northwickrealty.com</div>
    </footer>
  </main>
</body>
</html>
```